Ferncourt Labour Walk 2013

I am seeking to create a flyer promoting the event May Day in Sydney. The Event is a March and will be taking place on the 5th May Sunday. The Projection of the flyer should be fresh and modern but capable of encapsulating values of struggle, justice and solidarity. It is an event that started in the late 1800's in a struggle to obtain the 8 hour day.
This flyer should capture the old logo with a fresh modern interpretation.
Updates

HI All, 

Can we add the following details to design. Apologies it came late, it just got forwarded onto me. 

Twitter (logo) @FerncourtLabour
Facebook (logo) Labour Ferncourt 2013

Thanks

Reason: I want to allow designers the opportunity to make revisions on their existing designs.

Reason: Last minute changes are not coming through.

Target Market(s)

General Public, Union Members, Workers, advocates of social justice and democracy

Industry/Entity Type

Event

Requirements
Must have
• Event Details:
Ferncourt Labour Walk
Sunday May 5th
Assembling: 11:30am
Marching: 12:00pm
Assembly Point: Tindale Street outside Corvell Hall, Sydney
Ferncourt Labour Logo (See Attachment) This logo should be manipulated to show a fresh and modern aspect to it, whilst retaing the same characteristics.

Nice to have
• Themes of the flyer should capture the following ideas:
International Workers Solidarity
Workers Rights
Fight for the 8 hour day
location being Sydney Australia
Images of
People Rallying, protesting, marching

```html
<!DOCTYPE html>
<html lang="en">
<head>
<meta charset="utf-8">
<title>May Day Sydney Parade – Ferncourt Labour Walk 2013</title>
<link href="https://fonts.googleapis.com/css2?family=Oswald:wght@700&family=Archivo+Narrow:wght@700&family=Teko:wght@500&family=Roboto:wght@400&display=swap" rel="stylesheet">
<style>
  :root {
    --page-bg: #2b2b2b;
    --red-deep: #b3130f;
    --red-main: #d8271c;
    --red-light: #ec4a2f;
    --cream: #f0d48c;
    --ink: #1a1010;
    --white: #ffffff;
    --accent-red: #e0161b;
    --text-dark: #1b1b1b;
  }
  * { margin: 0; padding: 0; box-sizing: border-box; }
  html, body { width: 1200px; height: 900px; overflow: hidden; }
  body { background: var(--page-bg); position: relative; }

  .poster {
    position: absolute;
    left: 295px; top: 20px;
    width: 610px; height: 860px;
    background: var(--white);
    overflow: hidden;
  }
  .poster-field {
    position: absolute; left: 0; top: 0;
    width: 610px; height: 740px;
    background: linear-gradient(180deg, var(--red-deep) 0%, var(--red-main) 40%, var(--red-light) 75%, var(--red-main) 100%);
  }
  .poster-rays { position: absolute; left: 0; top: 0; }

  .scene-art {
    position: absolute; left: 0; top: 300px;
    width: 610px; height: 430px;
    background:
      linear-gradient(180deg, rgba(120,10,8,0) 0%, rgba(120,10,8,0.35) 40%, rgba(40,8,8,0.85) 78%, rgba(60,10,8,0.55) 100%);
  }

  .headline {
    position: absolute; left: 40px;
    font-family: 'Oswald', sans-serif; font-weight: 700;
    color: var(--cream); text-transform: uppercase; line-height: 1;
    white-space: nowrap; transform-origin: top left;
  }
  .headline--main { top: 18px; font-size: 134px; letter-spacing: 0; transform: scaleY(1.15); }
  .headline--sub { top: 172px; font-size: 78px; letter-spacing: 0; transform: scaleY(1.05); }
  .headline-rule {
    position: absolute; left: 40px; top: 266px;
    width: 532px; height: 3px; background: var(--cream);
  }
  .tagline {
    position: absolute; left: 40px; top: 278px;
    font-family: 'Oswald', sans-serif; font-weight: 700;
    color: var(--cream); font-size: 43px; line-height: 52px;
    text-transform: uppercase;
  }

  .placard {
    position: absolute;
    background: var(--ink); color: var(--red-light);
    font-family: 'Teko', sans-serif; font-weight: 500;
    text-transform: uppercase; text-align: center; line-height: 1;
  }
  .placard--workers { left: 10px; top: 428px; width: 90px; height: 60px; font-size: 22px; padding-top: 10px; }
  .placard--balance { left: 147px; top: 448px; width: 190px; height: 50px; font-size: 28px; padding-top: 13px; }
  .placard--solidarity { left: 345px; top: 465px; width: 130px; height: 50px; font-size: 28px; padding-top: 13px; }
  .placard--women { left: 512px; top: 460px; width: 74px; height: 88px; font-size: 20px; padding-top: 10px; }

  .event-date {
    position: absolute; left: 42px; top: 652px;
    font-family: 'Archivo Narrow', sans-serif; font-weight: 700;
    color: var(--cream); font-size: 48px; line-height: 1; white-space: nowrap;
  }
  .event-date sup { font-size: 22px; vertical-align: 22px; }

  .footer-curve { position: absolute; left: 0; top: 700px; }

  .details {
    position: absolute;
    font-family: 'Archivo Narrow', sans-serif; font-weight: 700;
    color: var(--text-dark); white-space: nowrap;
  }
  .details .label { color: var(--accent-red); }
  .details--times { left: 28px; top: 748px; font-size: 23px; line-height: 29px; }
  .details--place { left: 260px; top: 750px; font-size: 15px; line-height: 18px; }
  .social {
    position: absolute; top: 815px;
    font-family: 'Archivo Narrow', sans-serif; font-weight: 700;
    font-size: 19px; line-height: 1; color: var(--text-dark);
    display: flex; align-items: center; gap: 8px; white-space: nowrap;
  }
  .social--facebook { left: 28px; }
  .social--twitter { left: 260px; }
  .social-square { width: 18px; height: 18px; background: var(--accent-red); display: inline-block; }

  .committee-badge {
    position: absolute; left: 440px; top: 680px;
    width: 166px; height: 166px; border-radius: 50%;
    background: var(--accent-red);
    border: 5px solid var(--white);
    box-shadow: 0 0 0 2px var(--accent-red);
    display: flex; align-items: center; justify-content: center; text-align: center;
    font-family: 'Archivo Narrow', sans-serif; font-weight: 700;
    color: var(--white); font-size: 22px; line-height: 1.1; text-transform: uppercase;
  }

  .authorisation {
    position: absolute; left: 28px; top: 846px;
    font-family: 'Roboto', sans-serif; font-size: 7px; line-height: 1; color: var(--text-dark);
    white-space: nowrap;
  }
</style>
</head>
<body>
  <main class="poster">
    <div class="poster-field"></div>
    <svg class="poster-rays" width="610" height="740" viewBox="0 0 610 740" aria-hidden="true">
      <polygon points="0,0 610,40 610,70" fill="#ffffff" opacity="0.07"/>
      <polygon points="0,0 610,110 610,170" fill="#ffffff" opacity="0.06"/>
      <polygon points="0,0 610,230 610,290" fill="#ffffff" opacity="0.05"/>
      <polygon points="0,0 80,740 20,740" fill="#ffffff" opacity="0.05"/>
      <polygon points="0,0 30,0 610,10" fill="#ffffff" opacity="0.08"/>
    </svg>

    <div class="scene-art" role="img" aria-label="Illustration of the Sydney Harbour Bridge skyline behind a silhouetted crowd of marchers raising fists and banners"></div>

    <h1 class="headline headline--main">May Day</h1>
    <h2 class="headline headline--sub">Sydney Parade</h2>
    <div class="headline-rule"></div>
    <p class="tagline">A proud past,<br>a fighting future</p>

    <div class="placard placard--workers">Workers<br>Rights</div>
    <div class="placard placard--balance">Work Life Balance</div>
    <div class="placard placard--solidarity">Solidarity</div>
    <div class="placard placard--women">Women's<br>Rights<br>Now</div>

    <p class="event-date">Sunday May 5<sup>th</sup> 2013</p>

    <svg class="footer-curve" width="610" height="160" viewBox="0 0 610 160" aria-hidden="true">
      <path d="M0,30 Q300,12 610,40 L610,160 L0,160 Z" fill="#ffffff"/>
      <path d="M0,30 Q300,12 610,40" fill="none" stroke="#e0161b" stroke-width="4"/>
    </svg>

    <p class="details details--times">
      <span class="label">Assembling:</span> 11:30am<br>
      <span class="label">Marching:</span> 12:00pm
    </p>
    <p class="details details--place">
      <span class="label">Assembly Point:</span><br>
      Tindale Street outside<br>
      Corvell Hall, Sydney
    </p>

    <p class="social social--facebook"><span class="social-square"></span>Labour Ferncourt 2013</p>
    <p class="social social--twitter"><span class="social-square"></span>@FerncourtLabour</p>

    <div class="committee-badge">Ferncourt<br>Labour<br>Committee</div>

    <p class="authorisation">Authorised by Dana Whitlow, Secretary, Ferncourt Labour Committee, Level 2, 48 Orrin Street, Sydney NSW 2000</p>
  </main>
</body>
</html>
```